Ward Compass Business Card Design*

We need a business card design for our company Ward Compass. Our company is specialized in providing online consulting services regarding medical institutions, hospitals and doctors. We work with patients worldwide looking to choose between healthcare providers. We have a website you may use as a reference, where we list doctors and clinics worldwide. So we target Medical providers as well as patients worldwide.
Target Market(s)
Medical Providers and patients around the world
Industry/Entity Type
Medical
Contact Information for Business Card
Salwa Kettani
CEO
+90 612 348 2175
info@wardcompass.example
www.wardcompass.example
14 Annakhil 7 H.R.B. Rabat, Morocco
Requirements
Must have
- Company logo/name on one full side, personal info and smaller logo and company name on the other side.
Nice to have
- Smart and elegant design

```html
<!DOCTYPE html>
<html lang="en">
<head>
<meta charset="utf-8">
<title>Ward Compass – Business Card</title>
<link rel="stylesheet" href="https://fonts.googleapis.com/css2?family=Nunito+Sans:wght@400;600;700&display=swap">
<style>
  :root {
    --navy: #1b4475;
    --grey: #7d7d7f;
    --text-grey: #4f4f52;
    --rule-grey: #b3b3b5;
    --rule-violet: #8b86c4;
    --card-white: #f3f3f5;
    --stage: #e6e4e0;
    --white: #ffffff;
  }
  * { box-sizing: border-box; margin: 0; padding: 0; }
  html, body {
    width: 900px; height: 1200px; overflow: hidden;
    background: var(--stage);
    font-family: "Nunito Sans", Arial, sans-serif;
  }
  .canvas { position: relative; width: 900px; height: 1200px; }

  .card {
    position: absolute; left: 78px; width: 745px; height: 436px;
    box-shadow: 0 3px 8px rgba(0,0,0,0.18);
  }
  .card--front { top: 134px; background: var(--card-white); }
  .card--back { top: 639px; background: var(--navy); }

  /* brand lockup */
  .brand { position: absolute; display: flex; align-items: center; }
  .brand__dot { border-radius: 50%; flex: none; }
  .brand__name { font-weight: 600; letter-spacing: 0.01em; white-space: nowrap; }

  .card--front .brand { right: 40px; top: 76px; gap: 14px; }
  .card--front .brand__dot { width: 60px; height: 60px; background: var(--navy); }
  .card--front .brand__name { font-size: 27px; color: var(--navy); }

  .card--back .brand { left: 140px; top: 155px; gap: 26px; }
  .card--back .brand__dot { width: 120px; height: 120px; background: var(--white); }
  .card--back .brand__name { font-size: 43px; color: var(--white); }

  /* identity block */
  .accent-bar { position: absolute; left: 0; top: 214px; width: 27px; height: 43px; display: flex; }
  .accent-bar__navy { width: 19px; background: var(--navy); }
  .accent-bar__grey { width: 8px; background: var(--grey); }

  .person { position: absolute; left: 54px; top: 211px; }
  .person__name { font-size: 24px; line-height: 1.1; color: var(--text-grey); font-weight: 400; }
  .person__name strong { color: var(--navy); font-weight: 700; }
  .person__role { font-size: 17px; color: var(--text-grey); margin-top: 2px; }

  .rule { position: absolute; top: 252px; height: 1.5px; }
  .rule--violet { left: 111px; width: 160px; background: var(--rule-violet); }
  .rule--grey { left: 279px; width: 426px; background: var(--rule-grey); }

  /* contact */
  .contact { position: absolute; left: 54px; top: 358px; font-size: 17.5px; color: var(--text-grey); line-height: 22px; }
  .contact__row { display: flex; align-items: center; gap: 11px; }
  .contact__icon { width: 16px; height: 16px; fill: var(--navy); flex: none; }

  .address { position: absolute; right: 40px; top: 358px; font-size: 17.5px; color: var(--text-grey); line-height: 22px; text-align: left; }

  .website {
    position: absolute; left: 0; right: 0; top: 396px; text-align: center;
    color: var(--white); font-size: 16px; letter-spacing: 0.2em;
  }
</style>
</head>
<body>
<main class="canvas">

  <section class="card card--front" aria-label="Card front">
    <div class="brand">
      <span class="brand__dot"></span>
      <span class="brand__name">WARD COMPASS</span>
    </div>

    <div class="accent-bar"><span class="accent-bar__navy"></span><span class="accent-bar__grey"></span></div>
    <div class="person">
      <p class="person__name"><strong>SALWA</strong> KETTANI</p>
      <p class="person__role">CEO</p>
    </div>
    <span class="rule rule--violet"></span>
    <span class="rule rule--grey"></span>

    <div class="contact">
      <p class="contact__row">
        <svg class="contact__icon" viewBox="0 0 24 24" aria-hidden="true"><path d="M6.6 10.8a15.1 15.1 0 0 0 6.6 6.6l2.2-2.2c.3-.3.7-.4 1-.2 1.1.4 2.3.6 3.6.6.6 0 1 .4 1 1V20c0 .6-.4 1-1 1A17 17 0 0 1 3 4c0-.6.4-1 1-1h3.5c.6 0 1 .4 1 1 0 1.2.2 2.4.6 3.6.1.3 0 .7-.2 1z"/></svg>
        <span>+90 612 348 2175</span>
      </p>
      <p class="contact__row">
        <svg class="contact__icon" viewBox="0 0 24 24" aria-hidden="true"><path d="M2 5h20v14H2z M3.5 6.5 12 13l8.5-6.5" fill="var(--navy)" stroke="var(--card-white)" stroke-width="1.4"/></svg>
        <span>info@wardcompass.example</span>
      </p>
    </div>

    <address class="address" style="font-style:normal">
      14 Annakhil 7 H.R.B.<br>Rabat, Morocco
    </address>
  </section>

  <section class="card card--back" aria-label="Card back">
    <div class="brand">
      <span class="brand__dot"></span>
      <span class="brand__name">WARD COMPASS</span>
    </div>
    <p class="website">www.wardcompass.example</p>
  </section>

</main>
</body>
</html>
```